Webdesign für Zahnarztpraxis
Zielgruppe
Zahnarztpraxis
Aufgabenstellung
- Klares und übersichtliches Desgin
- Nicht zu verspielt
- Informativ
- Leichte Naviagtion
- Das Design der alten Webseite soll NICHT kopiert werden
- Die Farben Blau und Grün aus dem Logo sollen sich wiederfinden
- Designbeispiele, die dem Kunden gefallen sind https://www.falkmann-ostrup-zahnarztpraxis.de/ und https://www.zahvilkorn.de/

```html
<!DOCTYPE html>
<html lang="de">
<head>
<meta charset="utf-8">
<title>Dentalpraxis &amp; Labor Marie Kestner</title>
<link href="https://fonts.googleapis.com/css2?family=Inter:wght@400;500;600;700&display=swap" rel="stylesheet">
<style>
:root{
  --blue:#3b82f6;
  --blue-head:#3a86ec;
  --mint:#f5faee;
  --ink:#1f2328;
  --text:#3c4148;
  --white:#ffffff;
  --line:#d9dfe6;
}
*{box-sizing:border-box;margin:0;padding:0}
html,body{width:1200px;height:3301px;overflow:hidden}
body{font-family:"Inter",sans-serif;color:var(--text);background:var(--white);font-size:14px;line-height:1.6;position:relative}
.wrap{position:absolute;left:129px;right:129px}
a{color:inherit;text-decoration:none}

.topbar{position:absolute;top:0;left:0;width:1200px;height:38px;background:var(--mint);font-size:12px;color:var(--ink)}
.topbar .item{position:absolute;top:10px;display:flex;align-items:center;gap:8px}
.topbar svg{width:14px;height:14px}

.nav{position:absolute;top:38px;left:0;width:1200px;height:82px;background:var(--white)}
.brand{position:absolute;left:129px;top:24px;display:flex;align-items:center;gap:10px;font-weight:600;font-size:24px;color:var(--blue-head)}
.brand .dot{width:26px;height:26px;border-radius:50%;background:#7cc243}
.menu{position:absolute;right:129px;top:31px;display:flex;gap:26px;font-size:14px;color:var(--ink);font-weight:500}
.menu .active{color:var(--blue)}

.hero{position:absolute;top:120px;left:0;width:1200px;height:459px;background:linear-gradient(100deg,#c9c3bd 0%,#a89a93 30%,#e7a9a3 60%,#f1e2de 100%)}
.hero-box{position:absolute;left:129px;top:108px;width:383px;background:var(--blue);color:var(--white);padding:16px 17px 18px}
.hero-box h1{font-size:32px;line-height:1.2;font-weight:600}
.hero-box p{font-size:13px;margin-top:10px;line-height:1.65}

.notice{position:absolute;left:201px;top:524px;width:802px;height:109px;background:var(--mint);padding:22px 25px;font-size:13px;color:var(--ink);line-height:1.65}
.notice strong{font-weight:600}
.notice u{text-decoration:underline}

.photo{position:absolute;border-radius:6px}
.split-text{position:absolute;width:462px}
.split-text h2{font-size:33px;line-height:1.15;font-weight:500;color:var(--blue-head)}
.split-text p{font-size:13.5px;margin-top:16px;line-height:1.65}
.btn{display:inline-block;background:var(--blue);color:var(--white);font-weight:600;font-size:13.5px;padding:9px 17px;margin-top:20px}

.services{position:absolute;top:1098px;left:0;width:1200px;height:680px;background:var(--mint);text-align:center}
.services h2{margin-top:65px;font-size:33px;font-weight:500;color:var(--blue-head)}
.services .lead{font-size:13.5px;width:560px;margin:14px auto 0;line-height:1.65}
.card{position:absolute;width:175px;height:114px;background:var(--white);border-radius:6px;text-align:center;padding-top:16px;font-size:13px;font-weight:600;color:var(--ink);line-height:1.25}
.card svg{width:44px;height:44px;display:block;margin:0 auto 7px;fill:none;stroke:var(--blue);stroke-width:2;stroke-linecap:round;stroke-linejoin:round}

.footer{position:absolute;top:2812px;left:0;width:1200px;height:489px;background:var(--mint);font-size:13.5px;color:var(--ink)}
.footer h3{font-size:17px;font-weight:500;color:var(--blue-head);margin-bottom:10px}
.footer .col{position:absolute;top:34px}
.footer dt{font-weight:600}
.footer dd{margin-bottom:6px}
.hours{display:grid;grid-template-columns:98px auto;row-gap:6px}
.hours b{font-weight:600}
.legal{position:absolute;left:129px;top:451px;display:flex;gap:28px;font-size:12px}
</style>
</head>
<body>

<div class="topbar">
  <div class="item" style="left:129px">
    <svg viewBox="0 0 24 24" fill="none" stroke="#1f2328" stroke-width="2"><path d="M12 22s7-7 7-12a7 7 0 0 0-14 0c0 5 7 12 7 12z"/><circle cx="12" cy="10" r="2.5"/></svg>
    Lindenweg 14, 09876 Birkenau-Talheim
  </div>
  <div class="item" style="left:742px">
    <svg viewBox="0 0 24 24" fill="none" stroke="#1f2328" stroke-width="2"><path d="M5 3h4l2 5-3 2a11 11 0 0 0 6 6l2-3 5 2v4a2 2 0 0 1-2 2A17 17 0 0 1 3 5a2 2 0 0 1 2-2z"/></svg>
    03711-48260
  </div>
  <div class="item" style="left:862px">|</div>
  <div class="item" style="left:879px">
    <svg viewBox="0 0 24 24" fill="none" stroke="#1f2328" stroke-width="2"><rect x="3" y="5" width="18" height="14" rx="2"/><path d="M3 7l9 6 9-6"/></svg>
    info@zahnarztpraxis-kestner.de
  </div>
</div>

<header class="nav">
  <div class="brand"><span class="dot"></span>Kestner Dental</div>
  <nav class="menu">
    <a class="active">Start</a><a>Praxis</a><a>Eigenes Praxislabor</a><a>Leistungen</a><a>Unser Team</a><a>Anfahrt</a>
  </nav>
</header>

<section class="hero" role="img" aria-label="Nahaufnahme eines Lächelns mit zahnärztlichem Instrument">
  <div class="hero-box">
    <h1>Dentalpraxis &amp; Labor Marie Kestner</h1>
    <p>Ihre Zahnarztpraxis Kestner Birkenau-Talheim bietet die gesamte moderne Zahnheilkunde inklusive eigenem Praxislabor.</p>
  </div>
</section>

<div class="notice">
  <strong>Wichtige Information für unsere Patienten:</strong><br>
  Liebe Patientinnen und Patienten, unsere Praxis ist vom 17.02. bis 24.02. und am 28.02.2025 geschlossen.<br>
  Infomieren Sie sich bitte hier über Aktualisierungen auf unserem <u>Praxis-Eintrag bei Kartenportal</u>.
</div>

<div class="photo" style="left:129px;top:686px;width:462px;height:333px;background:linear-gradient(135deg,#e9ecef,#b9c3c6 55%,#5aa7a6)" role="img" aria-label="Behandlungsraum mit Zahnarztstuhl und Monitor"></div>
<div class="split-text" style="left:608px;top:716px">
  <h2>Zahnmedizin mit eigenem Labor und Fokus auf Prävention</h2>
  <p>Ihre moderne Praxis in Birkenau-Talheim bietet gesamte Zahnheilkunde und höchste Qualität durch das eigene Dentallabor. Unser Fokus liegt auf individueller Prävention für jedes Alter. Ihre Zahnärztin betreut Sie auf Wunsch auch fließend in Englisch.</p>
  <a class="btn">Unsere Praxis</a>
</div>

<section class="services">
  <h2>Unser umfassendes Leistungsspektrum</h2>
  <p class="lead">Von Diagnostik und Prophylaxe bis zu Prothetik und Chirurgie: Wir bieten Ihnen das komplette Spektrum der modernen Zahnheilkunde.</p>
  <a class="btn" style="margin-top:22px">Leistungen</a>
</section>

<!-- service cards -->
<svg width="0" height="0" style="position:absolute">
  <defs>
    <symbol id="tooth" viewBox="0 0 44 44"><path d="M14 8c-5 0-7 5-6 10 1 4 3 6 3 11 0 4 1 8 4 8s3-8 7-8 4 8 7 8 4-4 4-8c0-5 2-7 3-11 1-5-1-10-6-10-3 0-5 2-8 2s-5-2-8-2z"/></symbol>
  </defs>
</svg>
<div class="card" style="left:129px;top:1341px"><svg viewBox="0 0 44 44"><circle cx="26" cy="16" r="10"/><path d="M19 23L8 36"/><path d="M23 12c1-1 5-1 6 0v6h-6z"/></svg>Zahnärztliche<br>Diagnostik</div>
<div class="card" style="left:320px;top:1341px"><svg viewBox="0 0 44 44"><circle cx="20" cy="8" r="3"/><path d="M18 13v12h12l4 10M14 20v10h18M12 38h24"/></svg>Individual-<br>prophylaxe</div>
<div class="card" style="left:512px;top:1341px"><svg viewBox="0 0 44 44"><rect x="17" y="5" width="10" height="12" rx="1"/><path d="M22 17v22M27 8h4M27 12h4"/></svg>Professionelle<br>Zahnreinigung</div>
<div class="card" style="left:704px;top:1341px"><svg viewBox="0 0 44 44"><use href="#tooth" transform="translate(11 2) scale(.5)"/><path d="M6 22l6 12h8M38 22l-6 12h-8"/></svg>Konservierende<br>Zahnheilkunde</div>
<div class="card" style="left:895px;top:1341px"><svg viewBox="0 0 44 44"><rect x="14" y="5" width="16" height="8" rx="3"/><path d="M12 22h20l4 10H8zM6 36h32M18 13v9M26 13v9"/></svg>Zahnärztliche<br>Prothetik</div>

<div class="card" style="left:225px;top:1470px"><svg viewBox="0 0 44 44"><path d="M6 10h32v8c0 10-8 16-16 16S6 28 6 18z"/><path d="M12 12v6M18 12v6M26 12v6M32 12v6M8 20h28"/></svg>Kiefer-<br>orthopädie</div>
<div class="card" style="left:416px;top:1470px"><svg viewBox="0 0 44 44"><use href="#tooth" transform="translate(4 14) scale(.55)"/><path d="M24 26L36 8M33 6l6 4"/><path d="M4 38h36"/></svg>Chirurgische<br>Zahnheilkunde</div>
<div class="card" style="left:608px;top:1470px"><svg viewBox="0 0 44 44"><use href="#tooth" transform="translate(4 4) scale(.8)"/><path d="M34 4l1 3 3 1-3 1-1 3-1-3-3-1 3-1z"/></svg>Ästhetische<br>Zahnheilkunde</div>
<div class="card" style="left:800px;top:1470px"><svg viewBox="0 0 44 44"><use href="#tooth" transform="translate(11 8) scale(.5)"/><path d="M4 12V4h8M32 4h8v8M4 32v8h8M40 32v8h-8"/></svg>Ganzheitliche<br>Zahnheilkunde</div>

<div class="card" style="left:416px;top:1599px"><svg viewBox="0 0 44 44"><circle cx="22" cy="24" r="13"/><path d="M17 28c3 3 7 3 10 0M22 11c-2-3 2-6 4-3"/><circle cx="17" cy="22" r="1"/><circle cx="27" cy="22" r="1"/></svg>Kinderzahn-<br>heilkunde</div>
<div class="card" style="left:608px;top:1599px"><svg viewBox="0 0 44 44"><path d="M6 8h32v10c0 10-8 16-16 16S6 28 6 18z"/><path d="M12 10v8M18 10v8M26 10v8M32 10v8M8 26h28"/></svg>Bioverträglicher<br>Zahnersatz</div>

<div class="split-text" style="left:129px;top:1950px">
  <h2>Höchste Qualität, schnelle Ergebnisse: Unser eigenes Praxislabor</h2>
  <p>Kurze Wege und präzise Ergebnisse: Unsere Praxis verfügt über ein eigenes Dentallabor. Das sichert Ihnen biover­träglichen Zahnersatz und höchste Individualität direkt vor Ort.</p>
  <a class="btn">Eigenes Praxislabor</a>
</div>
<div class="photo" style="left:613px;top:1905px;width:462px;height:333px;background:linear-gradient(135deg,#e6b89a,#f1e6dc 45%,#d8d4cc 75%,#c9b24a)" role="img" aria-label="Zahntechnikerin bei der Arbeit im Praxislabor"></div>

<div class="photo" style="left:129px;top:2364px;width:462px;height:333px;background:linear-gradient(180deg,#f2f2f2,#e6e4e2 50%,#c9b8c0 80%,#a9b0c9)" role="img" aria-label="Gruppenfoto des Praxisteams"></div>
<div class="split-text" style="left:608px;top:2405px">
  <h2>Ihr Team für gesunde Zähne: Kompetent und immer für Sie da.</h2>
  <p>Lernen Sie uns kennen: Unser kompetentes und herzliches Praxisteam ist darauf fokussiert, Sie in allen Fragen der Zahngesundheit optimal zu unterstützen.</p>
  <a class="btn">Unser Team</a>
</div>

<footer class="footer">
  <div class="col" style="left:129px;width:300px">
    <div style="display:flex;align-items:center;gap:10px;font-weight:600;font-size:24px;color:var(--blue-head)"><span style="width:26px;height:26px;border-radius:50%;background:#7cc243"></span>Kestner Dental</div>
    <p style="margin-top:22px;line-height:1.6">Unsere Praxis bleibt in folgenden Zeiträumen wegen Praxisurlaub geschlossen:</p>
    <div class="hours" style="grid-template-columns:86px auto;row-gap:2px;margin-top:12px"><b>Winter</b><span>17.02.2025 – 24.02.2025</span><b>Schließtag</b><span>28.02.2025</span></div>
  </div>
  <div class="col" style="left:513px">
    <h3>So erreichen Sie uns</h3>
    <dl>
      <dt>Adresse</dt><dd>Lindenweg 14<br>09876 Birkenau-Talheim</dd>
      <dt>Telefon</dt><dd>03711-48260</dd>
      <dt>Fax</dt><dd>03711-48261</dd>
      <dt>E-Mail</dt><dd>info@zahnarztpraxis-kestner.de</dd>
    </dl>
  </div>
  <div class="col" style="left:773px">
    <h3>Öffnungszeiten</h3>
    <div class="hours">
      <b>Montag:</b><span>9:00 - 13:00 &amp; 14:00 - 19:00 Uhr</span>
      <b>Dienstag</b><span>9:00 - 13:00 &amp; 14:00 - 19:00 Uhr</span>
      <b>Mittwoch</b><span>9:00 - 14:00 Uhr</span>
      <b>Donnerstag</b><span>geschlossen</span>
      <b>Freitag</b><span>9:00 - 13:00 Uhr</span>
    </div>
    <p style="margin-top:10px">... und nach Vereinbarung</p>
    <h3 style="margin-top:22px;margin-bottom:4px">Telefonzeiten</h3>
    <p style="line-height:1.4;margin-bottom:12px">Innerhalb dieser Zeiten sind wir für<br>Sie telefonisch erreichbar:</p>
    <div class="hours" style="grid-template-columns:84px auto">
      <b>Montag:</b><span>9:00 - 15:00 Uhr</span>
      <b>Dienstag</b><span>9:00 - 15:00 Uhr</span>
      <b>Mittwoch</b><span>9:00 - 12:00 Uhr</span>
    </div>
  </div>
  <div class="legal"><span>Copyright ©2025</span><a>Impressum</a><a>Datenschutz</a><a>Cookie-Einstellungen</a></div>
</footer>

</body>
</html>
```